Accounting firm needing business card / letterhead designed
Marcus L. Trenholm, CPA
marcus@veltrowledger.com
www.veltrowledger.com
842 E Alder Ave Calder Ridge, OH 43827
419-562-0974

```html
<!DOCTYPE html>
<html lang="en">
<head>
<meta charset="utf-8">
<title>Veltro Ledger — Letterhead and Business Card</title>
<link rel="stylesheet" href="https://fonts.googleapis.com/css2?family=Roboto:wght@400;500&display=swap">
<style>
  :root {
    --navy: #272164;
    --green: #7dc242;
    --ink: #6b6b6b;
    --ink-dark: #3d3d3d;
    --rule: #9a9a9a;
    --paper: #ffffff;
    --stage: #e7e7e9;
  }
  * { box-sizing: border-box; margin: 0; padding: 0; }
  html, body { width: 1200px; height: 984px; overflow: hidden; }
  body {
    position: relative;
    background: var(--stage);
    font-family: "Roboto", Arial, sans-serif;
    color: var(--ink);
  }
  .sheet, .card {
    position: absolute;
    background: var(--paper);
    box-shadow: 0 4px 14px rgba(0,0,0,0.18);
    overflow: hidden;
  }
  .brand-name {
    font-family: "Roboto", Arial, sans-serif;
    font-weight: 500;
    color: var(--navy);
    text-transform: uppercase;
    letter-spacing: 0.06em;
    white-space: nowrap;
    line-height: 1;
  }
  .icon { width: 8px; height: 8px; fill: var(--ink-dark); vertical-align: -1px; margin-right: 5px; }
  .footer-band { position: absolute; left: 0; bottom: 0; display: block; }
  .footer-url {
    position: absolute; color: #fff; font-size: 9px; line-height: 1; letter-spacing: 0.02em;
  }

  /* Letterhead */
  .letterhead { left: 98px; top: 107px; width: 553px; height: 777px; }
  .letterhead .brand-name { position: absolute; left: 48px; top: 70px; font-size: 26px; }
  .letterhead .contact {
    position: absolute; left: 394px; top: 56px; font-size: 9px; line-height: 13px; color: var(--ink-dark);
  }
  .letterhead .contact .gap { margin-top: 3px; }
  .recipient { position: absolute; left: 48px; top: 229px; font-size: 10px; line-height: 14.5px; }
  .letter-body { position: absolute; left: 48px; top: 316px; width: 458px; font-size: 10px; line-height: 14.4px; text-align: justify; }
  .letter-body p + p { margin-top: 14px; }
  .signature {
    position: absolute; left: 48px; top: 518px; width: 106px; height: 66px;
    background: linear-gradient(135deg, rgba(39,33,100,0.12), rgba(39,33,100,0.04));
  }
  .sign-title { position: absolute; left: 48px; top: 605px; font-size: 10px; }
  .letterhead .footer-url { right: 37px; bottom: 8px; }

  /* Business card, front */
  .card { width: 380px; height: 217px; left: 710px; }
  .card-front { top: 251px; }
  .card-front .brand-name { position: absolute; left: 23px; top: 32px; font-size: 24px; }
  .holder-name { position: absolute; left: 23px; top: 105px; font-size: 16px; line-height: 18px; font-weight: 500; color: var(--navy); }
  .holder-role { position: absolute; left: 23px; top: 124px; font-size: 11px; line-height: 13px; color: var(--ink-dark); }
  .card-rule { position: absolute; left: 23px; top: 145px; width: 336px; border-top: 1px solid var(--rule); }
  .card-contact { position: absolute; left: 23px; top: 160px; font-size: 8.5px; line-height: 13px; color: var(--ink-dark); }
  .card-address { position: absolute; right: 21px; top: 163px; font-size: 8.5px; line-height: 12px; text-align: right; color: var(--ink-dark); }
  .card-front .footer-url { right: 20px; bottom: 5px; font-size: 8.5px; }

  /* Business card, back */
  .card-back { top: 510px; background: var(--navy); }
  .card-back .brand-name { position: absolute; left: 0; right: 0; top: 92px; text-align: center; font-size: 30px; color: #fff; }
  .card-back .back-url { position: absolute; left: 0; right: 0; top: 186px; text-align: center; font-size: 9px; color: #fff; }
</style>
</head>
<body>

  <section class="sheet letterhead">
    <div class="brand-name">Veltro Ledger</div>
    <div class="contact">
      <div>842 E Alder Ave Calder Ridge</div>
      <div>OH 43827</div>
      <div class="gap"><svg class="icon" viewBox="0 0 10 10"><path d="M2 0.5l2 2-1 1.3c.6 1.3 1.6 2.3 2.9 2.9l1.3-1 2 2-1.3 1.6C4.8 9.3.7 5.2.4 1.8z"/></svg>555-562-0974</div>
      <div><svg class="icon" viewBox="0 0 10 10"><path d="M0 1.5h10v1L5 5.5 0 2.5z M0 3.8l5 3 5-3V8.5H0z"/></svg>marcus@veltrowledger.com</div>
    </div>

    <div class="recipient">
      <div>Dear Hallorin</div>
      <div>Brevik Print Collective</div>
      <div>Department Design</div>
    </div>

    <div class="letter-body">
      <p>Lorem ipsum dolor sit amet, consectetuer adipiscing elit. Aenean commodo ligula eget dolor. Aenean massa. Cum sociis natoque penatibus et magnis dis parturient montes, nascetur ridiculus mus. Donec quam felis, ultricies nec, pellentesque eu, pretium quis, sem. Nulla consequat massa quis enim. Donec pede justo, fringilla vel, aliquet nec, vulputate eget, arcu. In enim justo, rhoncus ut, imperdiet a, venenatis vitae, justo. Nullam dictum felis eu pede mollis pretium. Integer tincidunt. Cras dapibus. Vivamus elementum semper nisi.Nullam dictum felis eu pede mollis pretium. Integer tincidunt. Cras dapibus. Vivamus elementum semper nisi.felis eu pede mollis pretium. Integer tincidunt. Cras dapibus.</p>
      <p>Quisque rutrum. Aenean imperdiet. Etiam ultricies nisi vel augue. Curabitur ullamcorper ultricies nisi. Nam eget dui. Etiam rhoncus. Maecenas tempus, tellus eget condimentum rhoncus, sem quam semper libero, sit amet adipiscing sem neque sed ipsum.felis pede mollis pretium. I am tincidunt. Cras dapibus.</p>
    </div>

    <div class="signature" role="img" aria-label="Handwritten signature of the director"></div>
    <div class="sign-title">Director/Excecutive Director</div>

    <svg class="footer-band" width="553" height="24" viewBox="0 0 553 24">
      <rect x="0" y="15" width="553" height="9" fill="var(--green)"/>
      <polygon points="372,0 553,0 553,24 356,24" fill="var(--navy)"/>
    </svg>
    <div class="footer-url">www.veltrowledger.com</div>
  </section>

  <section class="card card-front">
    <div class="brand-name">Veltro Ledger</div>
    <div class="holder-name">Marcus L. Trenholm</div>
    <div class="holder-role">CPA</div>
    <div class="card-rule"></div>
    <div class="card-contact">
      <div><svg class="icon" viewBox="0 0 10 10"><path d="M2 0.5l2 2-1 1.3c.6 1.3 1.6 2.3 2.9 2.9l1.3-1 2 2-1.3 1.6C4.8 9.3.7 5.2.4 1.8z"/></svg>555-562-0974</div>
      <div><svg class="icon" viewBox="0 0 10 10"><path d="M0 1.5h10v1L5 5.5 0 2.5z M0 3.8l5 3 5-3V8.5H0z"/></svg>marcus@veltrowledger.com</div>
    </div>
    <div class="card-address">
      <div>842 E Alder Ave Calder Ridge</div>
      <div>OH 43827</div>
    </div>
    <svg class="footer-band" width="380" height="19" viewBox="0 0 380 19">
      <rect x="0" y="11" width="380" height="8" fill="var(--green)"/>
      <polygon points="240,0 380,0 380,19 225,19" fill="var(--navy)"/>
    </svg>
    <div class="footer-url">www.veltrowledger.com</div>
  </section>

  <section class="card card-back">
    <div class="brand-name">Veltro Ledger</div>
    <div class="back-url">www.veltrowledger.com</div>
  </section>

</body>
</html>
```